Logistics Website Design

See website https://tqfreightglobal.com for theme and color details. Need the site to be re-done and reflect some of the designs shown in this list here: https://pixelvane.com/tags/logistics-company-website

Target Market(s)

Logistics & Transportation

Industry/Entity Type

Logistics and Supply Chain

Coding

Number of Pages Required

5+ page

Requirements
Must have
• Colors must match theme of logo. Looking for a sleek, interactive design.

```html
<!DOCTYPE html>
<html lang="en">
<head>
<meta charset="utf-8">
<title>TQ Freight Global — Logistics &amp; Transportation</title>
<link href="https://fonts.googleapis.com/css2?family=Poppins:wght@500;600;700&family=Lato:wght@400;700&display=swap" rel="stylesheet">
<style>
:root{
  --orange:#e4532b;
  --orange-light:#f0764f;
  --black:#0b0b0b;
  --dark:#1b1a1c;
  --text:#2b2b2b;
  --muted:#555;
  --white:#fff;
  --field:#fff;
}
*{box-sizing:border-box;margin:0;padding:0}
html,body{width:1200px;height:4518px;overflow:hidden;background:#fff}
body{font-family:'Lato',sans-serif;color:var(--text)}
.page{position:relative;width:1200px;height:4518px;overflow:hidden}
.abs{position:absolute}
h1,h2,h3,h4,.nav a,.btn{font-family:'Poppins',sans-serif}
.btn{display:inline-flex;align-items:center;justify-content:center;background:var(--orange);color:#fff;font-size:14px;font-weight:600;text-transform:uppercase;border-radius:3px;text-decoration:none;letter-spacing:.2px}
.brand{display:flex;align-items:center;gap:10px;color:#fff;font-family:'Poppins',sans-serif;font-weight:600}
.brand-dot{width:34px;height:34px;border-radius:50%;background:var(--orange);flex:none}

/* header */
.site-header{top:0;left:0;width:1200px;height:91px;background:var(--black)}
.site-header .brand{position:absolute;left:108px;top:28px;font-size:17px}
.nav{position:absolute;left:316px;top:36px;display:flex;gap:15px}
.nav a{color:#fff;font-size:14px;font-weight:500;text-decoration:none}
.nav a.active{color:var(--orange)}
.header-phone{position:absolute;left:763px;top:33px;display:flex;align-items:center;gap:8px;color:#fff;font-size:14px}
.icon-circle{display:flex;align-items:center;justify-content:center;border-radius:50%;background:var(--orange)}
.header-cta{position:absolute;left:935px;top:23px;width:156px;height:45px}

/* hero */
.hero{top:91px;left:0;width:1200px;height:620px}
.hero-photo{position:absolute;inset:0;background:linear-gradient(100deg,#2b2d33 0%,#4a4c52 35%,#7c4a3a 62%,#c0553a 74%,#5f6066 88%,#3a3b40 100%)}
.hero-photo::after{content:"";position:absolute;inset:0;background:linear-gradient(90deg,rgba(0,0,0,.55),rgba(0,0,0,0) 60%)}
.hero h1{position:absolute;left:109px;top:130px;color:#fff;font-size:48px;line-height:52px;font-weight:700;text-transform:uppercase}
.hero p{position:absolute;left:110px;top:249px;width:500px;color:#fff;font-size:15.5px;line-height:26px}
.hero .btn{position:absolute;left:110px;top:347px;width:155px;height:45px}
.hero svg{position:absolute;left:0;bottom:0}

/* welcome */
.welcome-text{left:112px;top:826px;width:450px}
.eyebrow{font-size:22px;font-weight:600;color:#111;text-transform:uppercase}
.welcome-text h2{margin-top:12px;color:var(--orange);font-size:30px;line-height:41px;font-weight:600;text-transform:uppercase}
.bar{width:70px;height:4px;background:var(--orange);margin-top:14px}
.welcome-text p{margin-top:18px;font-size:15px;line-height:26px;color:#333}
.welcome-text .btn{margin-top:20px;width:128px;height:45px}
.photo-grid{left:621px;top:828px;width:459px;height:401px;display:grid;grid-template-columns:218px 218px;grid-template-rows:190px 190px;gap:21px 23px}
.photo-grid div{border-radius:12px}
.ph1{background:linear-gradient(135deg,#2f7fa6,#c4563b 55%,#1f5f82)}
.ph2{background:linear-gradient(160deg,#9ec3e0,#3c5f85 60%,#7a3b2b)}
.ph3{background:linear-gradient(135deg,#cfd7dc,#3e4c5a 60%,#e18a2a)}
.ph4{background:linear-gradient(135deg,#d9dde0,#6b7a3a 55%,#2d2d2d)}
.grid-badge{left:793px;top:967px;width:114px;height:114px;border-radius:50%;background:#111;border:5px solid #fff}

/* industries */
.industries{top:1347px;left:0;width:1200px;height:533px;background:linear-gradient(120deg,#2a1f1c,#3d2a24 40%,#1c2430 70%,#2b2220)}
.industries::before{content:"";position:absolute;inset:0;background:rgba(0,0,0,.45)}
.ind-cards{position:absolute;left:110px;top:130px;display:flex;gap:24px}
.ind-card{width:228px;height:286px;border:1.5px solid #e6e6e6;border-radius:8px;text-align:center;color:#fff;padding:30px 12px 0}
.ind-card svg{display:block;margin:0 auto}
.ind-card h3{margin-top:14px;font-size:16px;font-weight:600;text-transform:uppercase;letter-spacing:.2px}
.ind-card p{margin-top:8px;font-size:14px;line-height:23.5px}

/* services */
.section-title{position:absolute;left:0;width:1200px;text-align:center;font-size:30px;font-weight:700;color:#111;text-transform:uppercase}
.title-bar{position:absolute;left:570px;width:60px;height:4px;background:var(--orange)}
.svc-card{position:absolute;width:318px;background:#fff;border-radius:6px;box-shadow:0 6px 12px rgba(228,83,43,.22);overflow:hidden;text-align:center}
.svc-img{height:247px}
.svc-card h3{font-size:16px;font-weight:600;text-transform:uppercase;color:#111;margin-top:30px}
.svc-card.featured{background:var(--orange);padding:0 12px 14px;height:491px}
.svc-card.featured .svc-img{margin:0 -12px}
.svc-card.featured .inner{background:#fff;border-radius:0 0 6px 6px;padding:20px 20px 20px;height:230px}
.svc-card.featured h3{margin-top:0;color:var(--orange);font-size:17px;line-height:27px}
.svc-card.featured p{margin-top:10px;font-size:15px;line-height:24px;color:#222}
.arrow{position:absolute;width:24px;height:24px;border:1.5px solid #555;border-radius:50%;display:flex;align-items:center;justify-content:center}

/* about */
.about{top:2657px;left:0;width:1200px;height:607px;background:linear-gradient(90deg,#151516 0%,#1f1f22 40%,#3a3028 65%,#6a4a30 80%,#2a3340 100%)}
.about-copy{position:absolute;left:110px;top:118px;width:485px;color:#fff}
.about-copy h2{font-size:30px;font-weight:700;text-transform:uppercase}
.about-copy .bar{margin-top:12px;width:55px}
.about-copy p{margin-top:14px;font-size:14.5px;line-height:24px}
.about-copy p+p{margin-top:20px}
.about-copy .btn{margin-top:20px;width:131px;height:45px}

/* contact */
.contact-info{left:138px;top:3463px}
.info-row{position:absolute;left:0;display:flex;gap:30px;width:400px}
.info-row .icon-circle{width:80px;height:80px}
.info-row h4{font-size:15px;font-weight:600;color:#111;margin-top:18px}
.info-row p{font-size:14.5px;line-height:26px;color:#222;margin-top:4px}
.form{left:486px;top:3464px;width:576px}
.field{position:absolute;background:var(--field);box-shadow:0 2px 8px rgba(0,0,0,.13);font-size:14px;color:#666;padding:14px 16px}
.form .btn{position:absolute;left:0;top:258px;width:118px;height:46px;font-size:16px;border-radius:0}

/* footer */
.footer{top:3885px;left:0;width:1200px;height:633px}
.footer-bg{position:absolute;inset:0}
.footer .brand{position:absolute;left:0;top:168px;width:1200px;justify-content:center;font-size:26px}
.footer .brand-dot{width:54px;height:54px}
.footer-nav{position:absolute;left:0;top:330px;width:1200px;display:flex;justify-content:center;gap:60px}
.footer-nav a{color:#fff;font-family:'Poppins',sans-serif;font-size:16px;text-decoration:none;text-transform:uppercase}
.rule{position:absolute;height:1px;background:#777}
.f-item{position:absolute;top:432px;display:flex;gap:14px;color:#fff}
.f-item .icon-circle{width:38px;height:38px;flex:none}
.f-item h4{font-size:18px;font-weight:600;text-transform:uppercase}
.f-item p{font-size:17px;line-height:28px}
.copyright{position:absolute;left:208px;top:580px;color:#fff;font-size:14px}
.socials{position:absolute;left:883px;top:572px;display:flex;gap:12px}
.socials span{width:32px;height:32px;border-radius:50%;background:var(--orange)}
</style>
</head>
<body>
<div class="page">

<header class="site-header abs">
  <div class="brand"><span class="brand-dot"></span>TQ Freight Global</div>
  <nav class="nav">
    <a class="active" href="#">HOME</a><a href="#">SERVICES</a><a href="#">INDUSTRIES</a><a href="#">ABOUT US</a><a href="#">CONTACT US</a>
  </nav>
  <div class="header-phone">
    <span class="icon-circle" style="width:24px;height:24px"><svg width="12" height="12" viewBox="0 0 24 24"><path fill="#fff" d="M6.6 10.8a15 15 0 0 0 6.6 6.6l2.2-2.2c.3-.3.7-.4 1-.2 1.1.4 2.3.6 3.6.6.6 0 1 .4 1 1V20c0 .6-.4 1-1 1A17 17 0 0 1 3 4c0-.6.4-1 1-1h3.5c.6 0 1 .4 1 1 0 1.3.2 2.5.6 3.6.1.3 0 .7-.2 1z"/></svg></span>
    +1 800 555 0199
  </div>
  <a class="btn header-cta" href="#">Request a quote</a>
</header>

<section class="hero abs">
  <div class="hero-photo" role="img" aria-label="Red semi-truck with a trailer parked at a logistics yard at sunset"></div>
  <h1>Delivering Strength<br>in Every Mile</h1>
  <p>We deliver a comprehensive range of open-deck and specialized transportation services—including flatbed, step deck, heavy haul, and over-dimensional freight solutions.</p>
  <a class="btn" href="#">Request a quote</a>
  <svg width="1200" height="130" viewBox="0 0 1200 130">
    <path d="M0 50 C250 95 450 110 620 110 C850 110 1050 60 1200 25 L1200 130 L0 130 Z" fill="#fff"/>
    <path d="M0 38 C250 80 440 100 600 100 C850 100 1050 50 1200 10 L1200 40 C1050 80 850 120 600 122 C420 122 230 95 0 55 Z" fill="var(--orange)"/>
    <path d="M0 55 C230 95 420 122 600 122 C850 120 1050 80 1200 40 L1200 55 C1050 95 850 130 600 130 C420 130 230 110 0 70 Z" fill="#fff"/>
  </svg>
</section>

<section class="welcome-text abs">
  <div class="eyebrow">Welcome to</div>
  <h2>Keeping your supply<br>chain moving</h2>
  <div class="bar"></div>
  <p>We deliver a comprehensive range of open-deck and specialized transportation services—including flatbed, step deck, heavy haul, and over-dimensional freight solutions. Backed by years of experience, a trusted nationwide carrier network, and a strong safety-first culture, we provide reliable, adaptable logistics support built around the unique requirements of every load.</p>
  <a class="btn" href="#">Read more</a>
</section>
<div class="photo-grid abs">
  <div class="ph1" role="img" aria-label="Container ship loaded with cargo at sea"></div>
  <div class="ph2" role="img" aria-label="Cargo plane above a container port"></div>
  <div class="ph3" role="img" aria-label="Forklift loading a truck at a warehouse dock"></div>
  <div class="ph4" role="img" aria-label="Two warehouse workers in safety vests reviewing a tablet"></div>
</div>
<div class="grid-badge abs"></div>

<section class="industries abs">
  <div class="ind-cards">
    <div class="ind-card">
      <svg width="66" height="50" viewBox="0 0 66 50" fill="none" stroke="#fff" stroke-width="3"><circle cx="33" cy="25" r="20"/><circle cx="33" cy="25" r="12"/><path d="M6 4v16M2 4v10a4 4 0 0 0 8 0V4M6 20v28M60 4c-4 4-4 14 0 18v26"/></svg>
      <h3>Food &amp; Beverage</h3>
      <p>TQ Freight provides reliable, compliant, and efficient trucking solutions for the food and beverage industry.</p>
    </div>
    <div class="ind-card">
      <svg width="60" height="50" viewBox="0 0 60 50" fill="none" stroke="#fff" stroke-width="3"><rect x="4" y="4" width="48" height="38" rx="3"/><path d="M4 12h48M14 20h4l4 12h16l3-9H20"/><circle cx="24" cy="36" r="2"/><circle cx="36" cy="36" r="2"/></svg>
      <h3>E-Commerce &amp; Retail</h3>
      <p>Our E-Commerce &amp; Retail Trucking Services are designed to support the fast-paced logistics demands of modern online</p>
    </div>
    <div class="ind-card">
      <svg width="60" height="50" viewBox="0 0 60 50" fill="none" stroke="#fff" stroke-width="3"><path d="M4 46V22l12 8v-8l12 8v-8l12 8V10h10v36Z"/><circle cx="30" cy="8" r="5"/><path d="M12 38h6M24 38h6M36 38h6"/></svg>
      <h3>Manufacturing</h3>
      <p>Industrial machinery and processing equipment often present unique challenges due to size, weight, and design.</p>
    </div>
    <div class="ind-card">
      <svg width="60" height="50" viewBox="0 0 60 50" fill="none" stroke="#fff" stroke-width="3"><path d="M6 46V18h48v28M2 46h56M24 46V34h12v12M30 4v10M25 9h10M12 26h6M42 26h6"/></svg>
      <h3>Pharma Healthcare</h3>
      <p>TQ Freight provides specialized transportation and supply chain solutions for pharmaceutical manufacturers</p>
    </div>
  </div>
</section>

<h2 class="section-title" style="top:1966px">Our Services</h2>
<div class="title-bar" style="top:2015px"></div>
<div class="arrow" style="left:48px;top:2186px"><svg width="10" height="10" viewBox="0 0 10 10"><path d="M6.5 1.5 3 5l3.5 3.5" stroke="#555" fill="none" stroke-width="1.5"/></svg></div>
<div class="arrow" style="left:1127px;top:2186px"><svg width="10" height="10" viewBox="0 0 10 10"><path d="M3.5 1.5 7 5 3.5 8.5" stroke="#555" fill="none" stroke-width="1.5"/></svg></div>
<div class="svc-card" style="left:98px;top:2056px;height:331px">
  <div class="svc-img" role="img" aria-label="Semi-truck hauling steel pipes on a flatbed trailer" style="background:linear-gradient(180deg,#9aa3ab,#5e6670 60%,#3b3f44)"></div>
  <h3>Flatbed Transportation</h3>
</div>
<div class="svc-card featured" style="left:441px;top:2056px">
  <div class="svc-img" role="img" aria-label="Delivery van at a container terminal" style="background:linear-gradient(180deg,#b9c4cc,#5b6f82 55%,#c0602f)"></div>
  <div class="inner">
    <h3>Dry Van<br>Transportation</h3>
    <p>From consumer goods to industrial materials, our dry van services provide the space, security, and consistency you need coast to coast.</p>
  </div>
</div>
<div class="svc-card" style="left:784px;top:2056px;height:331px">
  <div class="svc-img" role="img" aria-label="Yellow truck hauling logs on a step deck trailer" style="background:linear-gradient(180deg,#a8c3dc,#caa24a 55%,#4a4a4a)"></div>
  <h3>Step Deck Transportation</h3>
</div>

<section class="about abs" role="img" aria-label="Truck on a highway at dusk with a globe and airplane in the background">
  <div class="about-copy">
    <h2>Who we are</h2>
    <div class="bar"></div>
    <p><b>TQ Freight Global™</b> was born out of real-world experience in the fitness equipment industry. What started as a company shipping strength equipment, cardio machines, and training gear to gyms, schools, and commercial facilities quickly evolved into something bigger.</p>
    <p>As order volume grew and supply chains became more complex, the team developed deep expertise in coordinating freight, managing deliveries, and navigating the challenges of large-scale equipment transportation. That hands-on experience laid the foundation for what would eventually become a full-service logistics operation.</p>
    <a class="btn" href="#">Read more</a>
  </div>
</section>

<h2 class="section-title" style="top:3354px">Contact Us</h2>
<div class="contact-info abs">
  <div class="info-row" style="top:0">
    <span class="icon-circle"><svg width="34" height="26" viewBox="0 0 34 26"><rect x="1" y="1" width="32" height="24" rx="2" fill="#fff"/><path d="M2 3l15 12L32 3" stroke="var(--orange)" stroke-width="2.5" fill="none"/></svg></span>
    <div><h4>EMAIL:</h4><p>hello@tqfreightglobal.com</p></div>
  </div>
  <div class="info-row" style="top:105px">
    <span class="icon-circle"><svg width="30" height="30" viewBox="0 0 24 24"><path fill="#fff" d="M6.6 10.8a15 15 0 0 0 6.6 6.6l2.2-2.2c.3-.3.7-.4 1-.2 1.1.4 2.3.6 3.6.6.6 0 1 .4 1 1V20c0 .6-.4 1-1 1A17 17 0 0 1 3 4c0-.6.4-1 1-1h3.5c.6 0 1 .4 1 1 0 1.3.2 2.5.6 3.6.1.3 0 .7-.2 1z"/></svg></span>
    <div><h4>PHONE:</h4><p>+1 800 555 0199</p></div>
  </div>
  <div class="info-row" style="top:207px">
    <span class="icon-circle"><svg width="26" height="32" viewBox="0 0 24 30"><path d="M12 2a9 9 0 0 0-9 9c0 7 9 17 9 17s9-10 9-17a9 9 0 0 0-9-9z" fill="none" stroke="#fff" stroke-width="2.5"/><circle cx="12" cy="11" r="3.5" fill="#fff"/></svg></span>
    <div><h4>ADDRESS:</h4><p>0456 W. Example Ave.<br>#2040 Millbrook, CA 1234</p></div>
  </div>
</div>
<form class="form abs">
  <div class="field" style="left:0;top:0;width:283px;height:48px">First Name</div>
  <div class="field" style="left:293px;top:0;width:283px;height:48px">Last Name</div>
  <div class="field" style="left:0;top:63px;width:283px;height:48px">Phone Number</div>
  <div class="field" style="left:293px;top:63px;width:283px;height:48px">Email</div>
  <div class="field" style="left:0;top:126px;width:576px;height:111px">Message</div>
  <a class="btn" href="#">Submit</a>
</form>

<footer class="footer abs">
  <svg class="footer-bg" width="1200" height="633" viewBox="0 0 1200 633">
    <path d="M0 90 C300 20 550 5 800 20 C950 28 1080 50 1200 75 L1200 633 L0 633 Z" fill="var(--black)"/>
    <path d="M0 75 C300 5 560 -8 800 8 C960 18 1090 40 1200 62 L1200 82 C1080 55 950 34 800 26 C550 12 300 30 0 100 Z" fill="var(--orange)"/>
  </svg>
  <div class="brand"><span class="brand-dot"></span>TQ Freight Global</div>
  <nav class="footer-nav"><a href="#">Home</a><a href="#">About Us</a><a href="#">Service</a><a href="#">Industries</a><a href="#">Contact Us</a></nav>
  <div class="rule" style="left:133px;top:392px;width:934px"></div>
  <div class="f-item" style="left:205px">
    <span class="icon-circle"><svg width="18" height="18" viewBox="0 0 24 24"><path fill="#fff" d="M6.6 10.8a15 15 0 0 0 6.6 6.6l2.2-2.2c.3-.3.7-.4 1-.2 1.1.4 2.3.6 3.6.6.6 0 1 .4 1 1V20c0 .6-.4 1-1 1A17 17 0 0 1 3 4c0-.6.4-1 1-1h3.5c.6 0 1 .4 1 1 0 1.3.2 2.5.6 3.6.1.3 0 .7-.2 1z"/></svg></span>
    <div><h4>Phone:</h4><p>1800555019</p></div>
  </div>
  <div class="f-item" style="left:445px">
    <span class="icon-circle"><svg width="18" height="14" viewBox="0 0 34 26"><rect x="1" y="1" width="32" height="24" rx="2" fill="#fff"/><path d="M2 3l15 12L32 3" stroke="var(--orange)" stroke-width="3" fill="none"/></svg></span>
    <div><h4>E-mail:</h4><p>hello@tqfreightglobal.com</p></div>
  </div>
  <div class="f-item" style="left:762px">
    <span class="icon-circle"><svg width="14" height="18" viewBox="0 0 24 30"><path d="M12 2a9 9 0 0 0-9 9c0 7 9 17 9 17s9-10 9-17a9 9 0 0 0-9-9z" fill="#fff"/><circle cx="12" cy="11" r="3.5" fill="var(--orange)"/></svg></span>
    <div><h4>Address:</h4><p>42-44 Harbour Lane Riverton<br>NSW 2090 Australia</p></div>
  </div>
  <div class="rule" style="left:128px;top:556px;width:938px"></div>
  <p class="copyright">Copyright © 2026 TQ Freight Global™.All Rights Reserved</p>
  <div class="socials"><span></span><span></span><span></span><span></span></div>
</footer>

</div>
</body>
</html>
```